Journal Cover Design Project

The Worldwide Review of Rising Trade Systems is a professional journal which aims to provide an international platform for publication of original research on the emerging economies.
The journal is published three times a year and available by subscription. Currently, the cover design is the same for each issue. We are looking to redesign the cover (and interior) of our journal and would like a design that would allow us to change the color scheme for each issue or volume while maintaining a consistent design scheme.
Our design preference is simple and modern with good use of color. Many of our past publications have used abstract maps/globes but we are open to new ideas. We would need a creative way to include text on the cover, possibly a way to present the article titles or main topics for each issue. For example, we like the use of color and the general design in this image: http://www.pictavo.example/photos/moonlitpaperkite/5120448391/lightbox/
Below is a link to our most recent issue of the journal. You can see an example of the article titles, structure, etc. The website also shows the current cover of the journal (but we do not want the new design to be based off of the current one):
http://wrt.plovarhouse.example/content/4/2.toc

```html
<!DOCTYPE html>
<html lang="en">
<head>
<meta charset="utf-8">
<title>Worldwide Review of Rising Trade Systems — Volume 5, Issue 1</title>
<link rel="stylesheet" href="https://fonts.googleapis.com/css2?family=Arimo:wght@400;700&display=swap">
<style>
  :root {
    --page-bg: #ffffff;
    --cover-bg: #ffffff;
    --accent-red: #ef5b5b;
    --accent-green: #8cc63f;
    --ink: #1c1c1c;
    --rule: #111111;
    --globe-light: #f4f4f4;
    --globe-mid: #d6d6d6;
    --tower-light: #f6f6f6;
    --tower-mid: #e2e2e2;
    --label-bg: rgba(255, 255, 255, 0.92);
  }
  * { margin: 0; padding: 0; box-sizing: border-box; }
  html, body {
    width: 1001px;
    height: 1200px;
    overflow: hidden;
    background: var(--page-bg);
    font-family: "Arimo", Arial, sans-serif;
  }
  .stage {
    position: absolute;
    top: 0;
    left: 0;
    width: 830px;
    height: 995px;
    transform: scale(1.206);
    transform-origin: 0 0;
  }
  .cover {
    position: absolute;
    left: 57px;
    top: 18px;
    width: 718px;
    height: 945px;
    background: var(--cover-bg);
    box-shadow: 0 2px 10px rgba(0, 0, 0, 0.25);
    overflow: hidden;
  }
  .cover-art {
    position: absolute;
    inset: 0;
    width: 718px;
    height: 945px;
  }
  .issue-date {
    position: absolute;
    right: 20px;
    top: 158px;
    font-size: 20px;
    font-weight: 700;
    line-height: 1;
    color: #fff;
  }
  .masthead {
    position: absolute;
    left: 63px;
    top: 238px;
    line-height: 1;
  }
  .masthead-main {
    display: block;
    font-size: 62px;
    font-weight: 700;
    color: var(--accent-green);
    letter-spacing: -0.5px;
  }
  .masthead-sub {
    display: block;
    margin-top: 8px;
    font-size: 36px;
    font-weight: 700;
    color: var(--ink);
  }
  .feature {
    position: absolute;
    background: var(--label-bg);
    padding: 6px 8px 5px;
    color: var(--ink);
  }
  .feature-title {
    font-size: 28px;
    font-weight: 700;
    line-height: 1.08;
  }
  .feature-sub {
    font-size: 15px;
    font-weight: 700;
    line-height: 1.3;
  }
  .feature--gdp { left: 50px; top: 455px; }
  .feature--mexico { left: 42px; top: 560px; }
  .feature--mexico .feature-sub { font-size: 14px; }
  .feature--india { left: 55px; top: 680px; }
  .feature--water { left: 42px; top: 803px; }
  .volume-mark {
    position: absolute;
    left: 568px;
    top: 738px;
    width: 110px;
    height: 130px;
    color: var(--ink);
  }
  .volume-word {
    position: absolute;
    left: 0;
    top: 80px;
    font-size: 20px;
    font-weight: 700;
    line-height: 1;
    transform: rotate(90deg);
    transform-origin: 0 0;
    left: 34px;
    top: 8px;
  }
  .volume-number {
    position: absolute;
    left: 40px;
    top: -6px;
    font-size: 118px;
    font-weight: 700;
    line-height: 1;
    transform: scaleX(0.82);
    transform-origin: 0 0;
  }
  .issue-number {
    position: absolute;
    left: 4px;
    top: 98px;
    font-size: 22px;
    font-weight: 700;
    line-height: 1;
    white-space: nowrap;
  }
  .partners {
    position: absolute;
    left: 532px;
    top: 872px;
    display: flex;
    align-items: center;
    gap: 12px;
    color: var(--ink);
  }
  .partner {
    display: flex;
    align-items: center;
    gap: 5px;
    font-size: 10px;
    font-weight: 700;
    line-height: 1.1;
  }
  .partner-dot {
    width: 22px;
    height: 22px;
    border-radius: 50%;
    background: var(--ink);
    flex: none;
  }
</style>
</head>
<body>
<div class="stage">
  <article class="cover">
    <svg class="cover-art" viewBox="0 0 718 945" aria-hidden="false">
      <defs>
        <radialGradient id="globe-fill" cx="0.45" cy="0.4" r="0.6">
          <stop offset="0" stop-color="var(--globe-light)"/>
          <stop offset="1" stop-color="var(--globe-mid)"/>
        </radialGradient>
        <linearGradient id="tower-fill" x1="0" y1="0" x2="1" y2="0">
          <stop offset="0" stop-color="var(--tower-light)"/>
          <stop offset="0.5" stop-color="var(--tower-mid)"/>
          <stop offset="1" stop-color="var(--tower-light)"/>
        </linearGradient>
      </defs>
      <rect class="tower-area" x="300" y="120" width="360" height="290" fill="url(#tower-fill)" opacity="0.7" role="img" aria-label="Faint skyscraper rising behind the masthead"/>
      <rect class="header-band" x="0" y="0" width="718" height="130" fill="var(--accent-red)" role="img" aria-label="Red band with a fine woven line texture"/>
      <polygon class="header-band" points="0,0 718,0 718,130 0,114" fill="var(--accent-red)"/>
      <polygon class="header-accent" points="400,122 718,130 718,217 340,162" fill="var(--accent-green)"/>
      <rect x="0" y="112" width="718" height="2" fill="#fff" opacity="0"/>
      <polygon class="header-rule" points="0,112 718,214 718,219 0,117" fill="var(--rule)"/>
      <circle class="globe-area" cx="362" cy="700" r="330" fill="url(#globe-fill)" role="img" aria-label="Wireframe globe showing world continents"/>
      <polygon class="lower-accent" points="470,402 718,400 718,470" fill="var(--accent-green)"/>
      <polygon class="lower-rule" points="0,392 718,396 718,401 0,397" fill="var(--rule)"/>
      <rect class="footer-band" x="0" y="935" width="718" height="10" fill="var(--accent-green)"/>
    </svg>

    <div class="issue-date">08/2012</div>

    <h1 class="masthead">
      <span class="masthead-main">Worldwide Review</span>
      <span class="masthead-sub">of Rising Trade Systems</span>
    </h1>

    <section class="feature feature--gdp">
      <h2 class="feature-title">Construction and Analysis</h2>
      <p class="feature-sub">of a Global GDP Growth Model for<br>185 Countries through 2050</p>
    </section>

    <section class="feature feature--mexico">
      <h2 class="feature-title">A New Vision<br>for Mexico 2042</h2>
      <p class="feature-sub">Achieving Prosperity for All</p>
    </section>

    <section class="feature feature--india">
      <h2 class="feature-title">India 2039</h2>
      <p class="feature-sub">Transforming Agriculture:<br>Productivity, Markets,<br>and Institutions</p>
    </section>

    <section class="feature feature--water">
      <h2 class="feature-title">New Directions</h2>
      <p class="feature-sub">for Water Management in Indian Agriculture</p>
    </section>

    <div class="volume-mark">
      <span class="volume-word">VOLUME</span>
      <span class="volume-number">5</span>
      <span class="issue-number">ISSUE 1</span>
    </div>

    <div class="partners">
      <div class="partner">
        <span class="partner-dot"></span>
        <span>Rising<br>Markets<br>Circle</span>
      </div>
      <div class="partner">
        <span>Plovar<br>House</span>
      </div>
    </div>
  </article>
</div>
</body>
</html>
```